Brightway Carpet and Tile cleaning Business card Design

I need a design that has the same feel as my van.
i would also like a prominent "Review us on facebook" somewhere, but not that it makes it look silly.
I would like the card to have a little bit of grey or black in the design as well.

It will need contact details
phone: 0455 817264
email: rkbrightwayclean@mailbox-example.com
website: www.brightwaycarpetandtilecleaning-example.com.au
facebook: /brightwaycarpetandtilecleaning

Industry/Entity Type

Business

Contact Information for Business Card

Phone number 0455817264
Email rkbrightwayclean@mailbox-example.com
Website www.brightwaycarpetandtilecleaning-example.com.au
Facebook/brightwaycarpetandtilecleaning

Colors
000000

Requirements
Must have
• Same feel as my van
• I want the card to stand out from the crowd
Nice to have
• Maybe include a tiny bit of a third colour? Grey's,blacks, orange?

```html
<!DOCTYPE html>
<html lang="en">
<head>
<meta charset="utf-8">
<title>Brightway Carpet and Tile cleaning – Business Card</title>
<link href="https://fonts.googleapis.com/css2?family=Roboto:wght@300;400;700&display=swap" rel="stylesheet">
<style>
  :root {
    --backdrop: #bbbbbb;
    --card: #ffffff;
    --band: #5b5b5b;
    --brand-blue: #1aa3d9;
    --rule-blue: #3aaee0;
    --ink: #333333;
    --handle-grey: #8a8a8a;
  }
  * { margin: 0; padding: 0; box-sizing: border-box; }
  html, body { width: 1200px; height: 1200px; overflow: hidden; }
  body {
    background: var(--backdrop);
    font-family: "Roboto", Arial, sans-serif;
    position: relative;
  }
  .card {
    position: absolute;
    top: 185px;
    width: 460px;
    height: 753px;
    background: var(--card);
    overflow: hidden;
  }
  .card--front { left: 127px; }
  .card--back { left: 612px; }

  .brand {
    position: absolute;
    left: 0; right: 0;
    display: flex;
    align-items: center;
    justify-content: center;
    gap: 12px;
  }
  .brand__dot {
    width: 22px; height: 22px;
    border-radius: 50%;
    background: var(--brand-blue);
  }
  .brand__name {
    font-weight: 700;
    font-size: 46px;
    color: var(--brand-blue);
    letter-spacing: -0.5px;
  }
  .card--front .brand { top: 338px; }
  .card--back .brand { top: 122px; }

  .divider-band {
    position: absolute;
    left: 0; right: 0;
    top: 261px;
    height: 16px;
    background: var(--band);
  }

  .social-band {
    position: absolute;
    left: 0; right: 0;
    top: 643px;
    height: 34px;
    background: var(--band);
    display: flex;
    align-items: center;
    justify-content: center;
  }
  .social-band__mark {
    width: 26px; height: 26px;
    border: 2px solid var(--brand-blue);
  }
  .social-handle {
    position: absolute;
    left: 0; right: 0;
    top: 682px;
    text-align: center;
    font-weight: 300;
    font-size: 21px;
    color: var(--handle-grey);
  }
  .card--front .social-handle { padding-left: 20px; }

  .contact {
    position: absolute;
    left: 0; right: 0;
    text-align: center;
    color: var(--ink);
    font-weight: 400;
  }
  .contact--phone { top: 342px; font-size: 20px; }
  .contact--email { top: 440px; font-size: 17px; font-weight: 300; }
  .contact--web { top: 540px; font-size: 15px; font-weight: 300; }
  .contact-rule {
    position: absolute;
    left: 63px;
    width: 335px;
    height: 2px;
    background: var(--rule-blue);
  }
  .contact-rule--1 { top: 381px; }
  .contact-rule--2 { top: 503px; }
</style>
</head>
<body>
  <section class="card card--front" aria-label="Card front">
    <div class="brand">
      <span class="brand__dot"></span>
      <span class="brand__name">Brightway</span>
    </div>
    <div class="social-band"><span class="social-band__mark"></span></div>
    <p class="social-handle">brightwaycarpetandtilecleaning</p>
  </section>

  <section class="card card--back" aria-label="Card back">
    <div class="brand">
      <span class="brand__dot"></span>
      <span class="brand__name">Brightway</span>
    </div>
    <div class="divider-band"></div>
    <p class="contact contact--phone">0455 817264</p>
    <div class="contact-rule contact-rule--1"></div>
    <p class="contact contact--email">rkbrightwayclean@mailbox-example.com</p>
    <div class="contact-rule contact-rule--2"></div>
    <p class="contact contact--web">www.brightwaycarpetandtilecleaning-example.com.au</p>
    <div class="social-band"><span class="social-band__mark"></span></div>
    <p class="social-handle">brightwaycarpetandtilecleaning</p>
  </section>
</body>
</html>
```